Flyer Design for Upcoming Baseball Clinics, Camps, and Academies

What We Need:
We are looking for a design template we can use for our upcoming sports camps, clinics, and academies. We do elite level training with youth to professional athletes and brand awareness is our number one concern right now.

Ideally this template can be used across multiple sports. Here is our premise:

Clinics (1-Day Event to attract 50+ Athletes)
Camps (2-4 Day Events looking to attract 100+)
Academies (More intimate and skill specific. lasts 6-8 weeks. 10-20 athletes)

Our plan is to do this for Baseball, Football, Basketball, and Lacrosse.

The ideal situation is to be able to use this as a template so we can just edit the document in the future.

Target Market(s)

Prep: Middle School Athletes / ELITE: High School Athletes

Industry/Entity Type

Training

Requirements
Must have
• Things to include:
• Logo, Dates, Times, Investment, Description, Benefits, our mission statement, etc. Our specific colors, specific font family (Bunken Tech Sans Wide), follow our branding deck which is attached.
• Info:
• K7T BASEBALL CLINIC
• Date: November 11th, 2017
• AGES: PREP: (5th to 8th Grade). ELITE (9th-12th Grade)
• Registration: 8:00am - 9:00 am / 11:00 am - Noon
• Times:
• PREP: 9:00am - 11:00 am
• ELITE: Noon - 2pm
• Investment: $199
• Current Members: $99
Nice to have
• It would be nice to see our mission statement tied in somehow in a unique way. Also maybe a testimonial or two from our pro athletes??
Should not have
• Fake Images: Any Image used needs to be real and give off an authentic feel of a baseball player and the culture.

```html
<!DOCTYPE html>
<html lang="en">
<head>
<meta charset="utf-8">
<title>K7T Baseball Clinic Flyer</title>
<link rel="stylesheet" href="https://fonts.googleapis.com/css2?family=Michroma&family=Orbitron:wght@700;900&display=swap">
<style>
  :root {
    --page: #e9e6e2;
    --ink-dark: #0b0f10;
    --ink-mid: #18262a;
    --teal: #2b5a62;
    --teal-deep: #12292e;
    --cyan: #19b6e6;
    --white: #f2f4f5;
    --silver-hi: #f4f5f6;
    --silver-lo: #9a9ea2;
    --plate-text: #16191b;
  }
  * { box-sizing: border-box; margin: 0; padding: 0; }
  html, body { width: 1200px; height: 1200px; overflow: hidden; background: var(--page); }
  .flyer {
    position: absolute; left: 175px; top: 5px; width: 850px; height: 1190px;
    overflow: hidden;
    background:
      radial-gradient(ellipse at 50% 35%, var(--teal) 0%, var(--teal-deep) 45%, var(--ink-dark) 80%),
      var(--ink-dark);
    font-family: "Michroma", sans-serif; color: var(--white);
  }
  .flyer::after {
    content: ""; position: absolute; left: 0; right: 0; bottom: 0; height: 560px;
    background: linear-gradient(to bottom, rgba(11,15,16,0) 0%, rgba(11,15,16,0.85) 35%, var(--ink-dark) 100%);
    pointer-events: none;
  }
  .brand { position: absolute; left: 0; right: 0; top: 70px; text-align: center; z-index: 2; }
  .brand-name { font-family: "Michroma", sans-serif; font-size: 52px; letter-spacing: 2px; color: var(--white); }
  .brand-sub { margin-top: 40px; font-size: 8px; letter-spacing: 6px; color: var(--silver-lo); }
  .athletes {
    position: absolute; left: 60px; top: 260px; width: 770px; height: 420px; z-index: 1;
    background: radial-gradient(ellipse at 55% 45%, #5fa9b0 0%, #2e6a72 40%, rgba(18,41,46,0) 75%);
    opacity: 0.85;
  }
  .tilt { position: absolute; transform: rotate(-15deg); transform-origin: left center; z-index: 3; white-space: nowrap; }
  .accent-line { position: absolute; height: 3px; background: linear-gradient(to right, rgba(25,182,230,0), var(--cyan), rgba(25,182,230,0)); transform: rotate(-15deg); transform-origin: left center; z-index: 3; }
  .title-code {
    font-family: "Orbitron", sans-serif; font-weight: 900; font-size: 118px; line-height: 1;
    background: linear-gradient(to bottom, var(--silver-hi), var(--silver-lo));
    -webkit-background-clip: text; background-clip: text; color: transparent;
  }
  .title-event {
    font-family: "Orbitron", sans-serif; font-weight: 700; font-size: 46px; letter-spacing: 2px; line-height: 1;
    color: var(--silver-hi);
  }
  .plate {
    background: linear-gradient(to bottom, var(--silver-hi), var(--silver-lo));
    color: var(--plate-text); border: 2px solid #c9cccf; padding: 10px 16px;
  }
  .plate-date { font-family: "Orbitron", sans-serif; font-weight: 900; font-size: 22px; }
  .plate-price { font-size: 19px; }
  .plate-price strong { font-family: "Orbitron", sans-serif; font-weight: 900; font-size: 24px; }
  .info { font-size: 13px; line-height: 1.45; }
  .info-label { color: var(--cyan); font-size: 15px; }
  .info-indent { padding-left: 78px; }
</style>
</head>
<body>
  <main class="flyer">
    <header class="brand">
      <div class="brand-name">K7T</div>
      <div class="brand-sub">TRAINING HOUSE</div>
    </header>

    <div class="athletes" role="img" aria-label="Photo collage of athletes in action: lacrosse, football, basketball and baseball players"></div>

    <div class="accent-line" style="left:60px; top:760px; width:440px;"></div>
    <div class="accent-line" style="left:360px; top:870px; width:470px;"></div>

    <div class="tilt title-code" style="left:250px; top:660px;">K7T</div>
    <div class="tilt title-event" style="left:150px; top:820px;">BASEBALL CLINIC</div>

    <div class="tilt plate plate-date" style="left:225px; top:910px;">NOVEMBER 11TH, 2017</div>

    <div class="tilt info" style="left:440px; top:915px;">
      <span class="info-label">REGISTRATION:</span> 8:00AM - 9:00 AM<br>
      <span style="padding-left:170px;">11:00 AM - NOON</span>
    </div>

    <div class="tilt info" style="left:40px; top:1040px;">
      <span class="info-label">AGES:</span> PREP: (5TH TO 8TH GRADE)<br>
      <span class="info-indent">ELITE: (9TH-12TH GRADE)</span>
    </div>

    <div class="tilt info" style="left:50px; top:1110px;">
      <span class="info-label">TIMES:</span> PREP: 9:00AM - 11:00 AM<br>
      <span class="info-indent">ELITE: NOON - 2PM</span>
    </div>

    <div class="tilt plate plate-price" style="left:460px; top:1040px;">INVESTMENT: <strong>$199</strong></div>
    <div class="tilt plate plate-price" style="left:430px; top:1100px;">CURRENT MEMBERS: <strong>$99</strong></div>
  </main>
</body>
</html>
```